Software Development Consulting Company Needs Business Card Design

We need a new business card design for our consultants at Kestrel Works (kestrelworks.example). We are a small firm that provides high-end software development and methodology consulting to medium to large enterprise IT organizations.

Our logo uses Futura for the font and we would like to stick with navy blue and canary yellow for the logo colors. Attached are normal and reversed versions of our logos in illustrator format.
Updates

Hi Everyone, Thank yo very much for your amazing design ideas. I have created a poll for this project and our employees will be voting on the design they wish to use. We will be making a decision this Wednesday (October 22nd). Thanks again, Dale Hartwick

Industry/Entity Type

Business

```html
<!DOCTYPE html>
<html lang="en">
<head>
<meta charset="UTF-8">
<title>Kestrel Works — Business Card</title>
<link rel="stylesheet" href="https://fonts.googleapis.com/css2?family=Jost:wght@400;500&family=Open+Sans:wght@400;700&display=swap">
<style>
  :root {
    --navy: #1d4a73;
    --canary: #f2e600;
    --paper: #ffffff;
    --ink: #4a4a4a;
    --backdrop: #e9e6e1;
  }
  * { box-sizing: border-box; margin: 0; padding: 0; }
  html, body { width: 1200px; height: 720px; overflow: hidden; }
  body {
    background: var(--backdrop);
    font-family: "Open Sans", Arial, sans-serif;
    display: flex;
    align-items: center;
    justify-content: center;
    gap: 50px;
  }
  .card {
    width: 525px;
    height: 300px;
    background: var(--paper);
    box-shadow: 0 6px 18px rgba(0,0,0,0.15);
    position: relative;
    display: flex;
    flex-direction: column;
  }
  .band {
    background: var(--navy);
    color: var(--paper);
    display: flex;
    align-items: center;
    justify-content: center;
    height: 44px;
  }
  .band--top { border-bottom: 3px solid var(--canary); }
  .band--bottom { border-top: 3px solid var(--canary); margin-top: auto; }
  .holder-name { font-weight: 700; font-size: 17px; }
  .holder-name .title { font-weight: 400; font-size: 13px; }
  .locations { font-size: 15px; letter-spacing: 0.5px; }
  .card-body {
    flex: 1;
    display: flex;
    flex-direction: column;
    align-items: center;
    justify-content: center;
    gap: 22px;
  }
  .wordmark {
    display: flex;
    align-items: center;
    gap: 12px;
    font-family: "Jost", Futura, sans-serif;
    font-weight: 500;
    color: var(--navy);
    letter-spacing: 4px;
    text-transform: uppercase;
    white-space: nowrap;
  }
  .wordmark__dot {
    width: 14px; height: 14px; border-radius: 50%;
    background: var(--canary);
    flex: none;
  }
  .wordmark--front { font-size: 36px; }
  .contact {
    display: grid;
    grid-template-columns: auto auto;
    gap: 6px 26px;
    justify-content: center;
    font-size: 13px;
    color: var(--ink);
  }
  .contact__item { display: flex; align-items: center; gap: 6px; white-space: nowrap; }
  .contact__item--web { grid-column: 1 / span 2; justify-self: center; }
  .icon { width: 13px; height: 13px; fill: var(--ink); flex: none; }
  .card--back { align-items: center; justify-content: center; gap: 54px; padding-top: 20px; }
  .wordmark--back { font-size: 34px; }
  .back-url {
    font-size: 17px;
    letter-spacing: 4px;
    color: var(--ink);
    white-space: nowrap;
  }
</style>
</head>
<body>

  <section class="card card--front" aria-label="Card front">
    <header class="band band--top">
      <p class="holder-name">Your Name, <span class="title">Title</span></p>
    </header>
    <div class="card-body">
      <div class="wordmark wordmark--front">
        <span class="wordmark__dot"></span>
        <span>Kestrel Works</span>
      </div>
      <div class="contact">
        <span class="contact__item">
          <svg class="icon" viewBox="0 0 16 16"><circle cx="8" cy="8" r="8"/><path d="M5 4l2 2-1 1.2c.6 1.3 1.5 2.2 2.8 2.8L10 9l2 2-1.2 1.2C7.5 12 4 8.5 3.8 5.2z" fill="#fff"/></svg>
          012-555-0147
        </span>
        <span class="contact__item">
          <svg class="icon" viewBox="0 0 16 16"><rect x="1" y="3" width="14" height="10" rx="1.5"/><path d="M2 4l6 5 6-5" stroke="#fff" stroke-width="1.3" fill="none"/></svg>
          info@kestrelworks.example
        </span>
        <span class="contact__item contact__item--web">
          <svg class="icon" viewBox="0 0 16 16"><circle cx="8" cy="8" r="8"/><path d="M1 8h14M8 1v14M8 1c-3 3-3 11 0 14M8 1c3 3 3 11 0 14" stroke="#fff" stroke-width="1" fill="none"/></svg>
          www.kestrelworks.example
        </span>
      </div>
    </div>
    <footer class="band band--bottom">
      <p class="locations">Ashford + Millbrook, OR</p>
    </footer>
  </section>

  <section class="card card--back" aria-label="Card back">
    <div class="wordmark wordmark--back">
      <span class="wordmark__dot"></span>
      <span>Kestrel Works</span>
    </div>
    <p class="back-url">www.kestrelworks.example</p>
  </section>

</body>
</html>
```